Velundra Jobs portal

Velundra Jobs is a job portal connecting job seekers and companies offering part time jobs in the Mena region, starting in the UAE. We would like to see designs that use the color blue. We have attached images to give an idea what the website should look like. When a company posts a job the job seekers are not allowed to see which company has posted a job. There should also be a coinvex gateway. On the landing page we want a catching picture that we will send.

Target Market(s)

Students and promotional workers

Logo Text

Velundra Jobs

Coding

Coded - Design and coding required

Number of Pages Required

4 page

Font styles to use
Sans Serif

Colors
33a6d7
0692cd
85cae6

```html
<!DOCTYPE html>
<html lang="en">
<head>
<meta charset="utf-8">
<title>Velundra Jobs</title>
<link rel="stylesheet" href="https://fonts.googleapis.com/css2?family=Oswald:wght@300;600&family=Open+Sans:wght@400;600&display=swap">
<style>
  :root {
    --hero-deep: #2f5675;
    --hero-mid: #5f88a8;
    --hero-light: #9fbdd3;
    --figure-tone: rgba(62, 58, 58, 0.55);
    --crowd-tone: rgba(18, 38, 58, 0.45);
    --brand-blue: #2d5ba6;
    --button-blue: #2a55a3;
    --button-blue-top: #3563b2;
    --button-pink: #e04b8c;
    --button-pink-top: #e9609c;
    --logo-teal: #7fd6e6;
    --ring: rgba(255, 255, 255, 0.85);
    --white: #ffffff;
  }
  * { box-sizing: border-box; margin: 0; padding: 0; }
  html, body { width: 1200px; height: 686px; overflow: hidden; }
  body {
    position: relative;
    font-family: "Open Sans", Arial, sans-serif;
    color: var(--white);
    background: var(--hero-deep);
  }
  .hero {
    position: absolute; left: 0; top: 0; width: 1200px; height: 614px;
    background:
      radial-gradient(ellipse 300px 420px at 170px 470px, var(--figure-tone), transparent 75%),
      radial-gradient(ellipse 420px 220px at 930px 480px, var(--crowd-tone), transparent 80%),
      radial-gradient(ellipse 520px 300px at 700px 120px, var(--hero-light), transparent 70%),
      linear-gradient(180deg, var(--hero-mid) 0%, var(--hero-deep) 55%, var(--hero-mid) 100%);
  }
  .brand {
    position: absolute; left: 96px; top: 150px;
    display: flex; align-items: center; gap: 8px;
    font-family: "Open Sans", Arial, sans-serif; font-weight: 600;
    font-size: 28px; line-height: 40px; color: var(--logo-teal);
  }
  .brand-dot {
    width: 14px; height: 14px; border-radius: 50%; background: var(--logo-teal);
  }
  .social {
    position: absolute; left: 849px; top: 68px; display: flex; gap: 6px;
  }
  .social-ring {
    width: 36px; height: 36px; border-radius: 50%;
    border: 2px solid var(--ring);
  }
  .social-ring.active { background: var(--brand-blue); }
  .menu-toggle { position: absolute; left: 1078px; top: 77px; }
  .headline {
    position: absolute; left: 0; top: 270px; width: 1200px; text-align: center;
    font-family: "Oswald", "Arial Narrow", sans-serif;
  }
  .headline-main { font-weight: 600; font-size: 28px; line-height: 40px; }
  .headline-sub { font-weight: 300; font-size: 28px; line-height: 40px; margin-top: 7px; }
  .actions {
    position: absolute; left: 386px; top: 379px; display: flex; gap: 13px;
  }
  .action {
    width: 135px; height: 39px; border-radius: 2px;
    display: flex; align-items: center; justify-content: center;
    font-size: 12px; color: var(--white); text-decoration: none;
    background: linear-gradient(180deg, var(--button-blue-top), var(--button-blue));
  }
  .action.highlight { background: linear-gradient(180deg, var(--button-pink-top), var(--button-pink)); }
  .site-footer {
    position: absolute; left: 0; top: 614px; width: 1200px; height: 72px;
    background: var(--brand-blue); font-size: 11px;
  }
  .site-footer span, .site-footer a {
    position: absolute; top: 29px; color: var(--white); text-decoration: none;
  }
</style>
</head>
<body>
  <div class="hero" role="img" aria-label="Photo of a businessman pointing at a skyline with silhouettes of professionals"></div>

  <div class="brand"><span class="brand-dot"></span>Velundra Jobs</div>

  <nav class="social" aria-label="Social links">
    <span class="social-ring active"></span>
    <span class="social-ring"></span>
    <span class="social-ring"></span>
    <span class="social-ring"></span>
    <span class="social-ring"></span>
  </nav>

  <svg class="menu-toggle" width="22" height="20" viewBox="0 0 22 20" aria-label="Menu">
    <rect x="0" y="0" width="22" height="4" rx="1" fill="#fff"/>
    <rect x="0" y="8" width="22" height="4" rx="1" fill="#fff"/>
    <rect x="0" y="16" width="22" height="4" rx="1" fill="#fff"/>
  </svg>

  <div class="headline">
    <h1 class="headline-main">NUMBER ONE PLATFORM CONNECTING PEOPLE</h1>
    <p class="headline-sub">WITH EVENTS COMPANIES</p>
  </div>

  <div class="actions">
    <a class="action" href="#">Join Velundra</a>
    <a class="action" href="#">Employer</a>
    <a class="action highlight" href="#">Job Seeker</a>
  </div>

  <footer class="site-footer">
    <span style="left:99px">Copyrights © Velundra 2015 . All Rights Reserved</span>
    <a href="#" style="left:830px">About us</a>
    <a href="#" style="left:911px">Terms and conditions</a>
    <a href="#" style="left:1058px">Sitemap</a>
    <span style="left:1145px">C12</span>
  </footer>
</body>
</html>
```